Stationery Design Project for Nimbora, Chicago

Nimbora, a street parking application which helps car drivers find a street parking spot by offering an ideal path along which to look for parking. This path is calculated by our algorithm based on data (e.g. historical data, baseball games schedule, etc.). Along this path the driver will find a spot and will also save 70% of the search time. Customer we target is reg. between 21 and 45 yo.

We envision something young, fresh, bright and original. Slightly abstract maybe. It should represent the idea and elements of finding street parking in the city, e.g. car(s), parking spot, people, city, etc. (just ideas!).

Logo is attached.

Requirement:
- Business Cards (2 Sided Full Color CMYK)
- Letterhead (1 Sided Full Color CMYK)
- Envelope (1 Sided Full Color CMYK)
- Sticker (1 Sided Full Color CMYK), round with a 2inch diameter.

Reason: We're starting to get more and more designs and need more time to look into all of them. Very exciting!! Thanks to everybody!

Hi all, we're in the process of selecting our favs. Though choices!!! Really good submissions. Will keep you posted and sorry for the delay.

Target Market(s)

Car drivers and owners between 21 and 45

Industry/Entity Type

Parking

Requirements
Must have
• Sticker should be round and include company URL nimbora.com and the new logo which we will attach soon.
Should not have
• Should not be too serious or boring.

```html
<!DOCTYPE html>
<html lang="en">
<head>
<meta charset="utf-8">
<title>Nimbora Business Card</title>
<link rel="stylesheet" href="https://fonts.googleapis.com/css2?family=Open+Sans:wght@400;600;700&display=swap">
<style>
  :root {
    --backdrop: #d6d6d6;
    --card-light: #f4f4f4;
    --card-mid: #dcdcdc;
    --brand-blue: #26349a;
    --brand-blue-bright: #1a7fd0;
    --band-dark: #3a3a3a;
    --band-black: #0d0d0d;
    --ink: #1f1f1f;
    --ink-soft: #4a4a4a;
    --rule: #555555;
  }
  * { margin: 0; padding: 0; box-sizing: border-box; }
  html, body {
    width: 944px; height: 1200px; overflow: hidden;
    background: var(--backdrop);
    font-family: "Open Sans", Arial, sans-serif;
  }
  .canvas { position: relative; width: 944px; height: 1200px; }
  .card {
    position: absolute; left: 87px; width: 789px; height: 450px;
    border-radius: 28px; overflow: hidden;
    box-shadow: 0 4px 10px rgba(0,0,0,0.25);
  }
  .card--front { top: 98px; }
  .card--back { top: 636px; }
  .card__art { position: absolute; inset: 0; width: 789px; height: 450px; }
  .brand {
    position: absolute; left: 190px; top: 68px;
    display: flex; align-items: center; gap: 26px;
  }
  .brand__dot {
    width: 146px; height: 146px; border-radius: 50%;
    background: var(--brand-blue);
  }
  .brand__name {
    font-size: 82px; font-weight: 600; color: var(--ink);
    letter-spacing: -1px; line-height: 1;
  }
  .holder {
    position: absolute; right: 307px; top: 290px; text-align: right;
  }
  .holder__name { font-size: 24px; font-weight: 700; color: var(--ink-soft); line-height: 30px; }
  .holder__role { font-size: 18px; color: var(--ink-soft); line-height: 28px; }
  .divider {
    position: absolute; left: 511px; top: 268px; width: 2px; height: 98px;
    background: var(--rule);
  }
  .contacts {
    position: absolute; left: 532px; top: 262px;
    list-style: none; font-size: 18.5px; color: var(--ink-soft); line-height: 26px;
  }
  .contacts b { color: var(--ink); font-weight: 700; }
  .address {
    position: absolute; right: 42px; top: 398px;
    font-size: 18.5px; color: var(--ink-soft);
  }
  .back-mark {
    position: absolute; left: 186px; top: 165px;
    width: 146px; height: 146px; border-radius: 50%;
    background: var(--brand-blue);
  }
  .web {
    position: absolute; left: 403px; top: 224px;
    font-size: 20px; letter-spacing: 5px; color: var(--ink-soft);
  }
  .web b { color: var(--ink); font-weight: 700; letter-spacing: 6px; }
</style>
</head>
<body>
<div class="canvas">

  <section class="card card--front">
    <svg class="card__art" viewBox="0 0 789 450" aria-hidden="true">
      <defs>
        <linearGradient id="faceLight" x1="0" y1="0" x2="1" y2="1">
          <stop offset="0" stop-color="#fbfbfb"/>
          <stop offset="1" stop-color="#d9d9d9"/>
        </linearGradient>
        <radialGradient id="bandBlue" cx="0.25" cy="0.3" r="0.8">
          <stop offset="0" stop-color="#1e6fc4"/>
          <stop offset="1" stop-color="#26349a"/>
        </radialGradient>
      </defs>
      <rect width="789" height="450" fill="url(#faceLight)"/>
      <path d="M0 0 H295 C150 90 105 320 168 450 H0 Z" fill="url(#bandBlue)"/>
      <path d="M195 0 H255 C130 100 90 300 118 390 C60 290 85 120 195 0 Z" fill="#ffffff"/>
      <path d="M255 0 H295 C150 90 105 320 168 450 H150 C95 330 120 110 255 0 Z" fill="#1a7fd0"/>
    </svg>
    <div class="brand">
      <span class="brand__dot"></span>
      <span class="brand__name">Nimbora</span>
    </div>
    <div class="holder">
      <p class="holder__name">Your Name</p>
      <p class="holder__role">Designation</p>
    </div>
    <span class="divider"></span>
    <ul class="contacts">
      <li><b>p</b> : 123-456-7890</li>
      <li><b>c</b> : 123-456-7890</li>
      <li><b>e</b> : name@website.com</li>
      <li><b>w</b> : www.website.com</li>
    </ul>
    <p class="address">City Name, Street Name, State Name, Country Code</p>
  </section>

  <section class="card card--back">
    <svg class="card__art" viewBox="0 0 789 450" aria-hidden="true">
      <defs>
        <linearGradient id="faceLightBack" x1="0" y1="0" x2="1" y2="1">
          <stop offset="0" stop-color="#fbfbfb"/>
          <stop offset="1" stop-color="#d9d9d9"/>
        </linearGradient>
        <radialGradient id="bandDark" cx="0.3" cy="0.3" r="0.8">
          <stop offset="0" stop-color="#8a8a8a"/>
          <stop offset="1" stop-color="#3a3a3a"/>
        </radialGradient>
      </defs>
      <rect width="789" height="450" fill="url(#faceLightBack)"/>
      <path d="M0 0 H295 C150 90 105 320 168 450 H0 Z" fill="url(#bandDark)"/>
      <path d="M195 0 H255 C130 100 90 300 118 390 C60 290 85 120 195 0 Z" fill="#ffffff"/>
      <path d="M255 0 H295 C150 90 105 320 168 450 H150 C95 330 120 110 255 0 Z" fill="#0d0d0d"/>
    </svg>
    <span class="back-mark"></span>
    <p class="web">www.<b>website</b>.com</p>
  </section>

</div>
</body>
</html>
```